Building company buisness cards

We are looking for a sharp modern new look for our business cards.
We are a New Zealand based company that specialises in house and land packages.
We have attached a photo of the current logo and would like to see if it can be improved somehow if needed.
We are open to any colours but we have chosen green at this stage.
Feel free to change the font and make the logo smarter looking.
Play with the colours and see what looks best.

We want a card that looks so good know one will want to throw it away!

Target Market(s)

Home buyers

Industry/Entity Type

Building

Contact Information for Business Card

Derek Tolvane
0217394062
dtolvane@quillmarkhomesteads.co.nz
quillmarkhomesteads.co.nz

Font styles to use
Serif
Sans Serif

Colors

Designer to choose colors to be used in the design.

Requirements
Must have
• Logo and company name on one side, details on the other side
Nice to have
• Color codes for the original green are HEX #4a8028, RGB(74,128,40), CMYK(42,0,69,50)
• Round corners, Raised and/or spot UV

```html
<!DOCTYPE html>
<html lang="en">
<head>
<meta charset="utf-8">
<title>Quillmark Homesteads – Business Cards</title>
<link rel="stylesheet" href="https://fonts.googleapis.com/css2?family=Arimo:wght@700&family=Open+Sans:wght@400;800&display=swap">
<style>
  :root {
    --backdrop: #c8c9cb;
    --brand-green: #4a8028;
    --band-grey: #6b6b6b;
    --card-white: #ffffff;
    --ink: #222222;
  }
  * { margin: 0; padding: 0; box-sizing: border-box; }
  html, body { width: 1200px; height: 1015px; overflow: hidden; }
  body { background: var(--backdrop); position: relative; font-family: "Open Sans", Arial, sans-serif; }

  .card {
    position: absolute;
    width: 687px;
    height: 393px;
    border-radius: 30px;
    overflow: hidden;
    box-shadow: 0 3px 8px rgba(0,0,0,0.18);
  }
  .card-front { left: 416px; top: 80px; background: var(--card-white); border: 1px solid #444; }
  .card-back { left: 118px; top: 533px; background: var(--band-grey); }

  .wave { position: absolute; left: 0; top: 0; width: 687px; height: 393px; }

  .holder-name {
    position: absolute; right: 45px; top: 36px;
    font-family: "Arimo", Arial, sans-serif; font-weight: 700;
    font-size: 30px; color: var(--card-white); line-height: 1;
  }

  .brand { position: absolute; text-align: center; }
  .brand-mark { display: block; margin: 0 auto; border-radius: 50%; }
  .brand-name {
    font-family: "Open Sans", Arial, sans-serif; font-weight: 800;
    line-height: 1.05; letter-spacing: -0.5px;
  }
  .brand-rule { display: block; margin: 0 auto; height: 2px; }

  .card-front .brand { left: 20px; top: 78px; width: 326px; }
  .card-front .brand-mark { width: 40px; height: 40px; background: var(--brand-green); }
  .card-front .brand-name { color: var(--brand-green); font-size: 33px; margin-top: 20px; }
  .card-front .brand-rule { width: 121px; background: var(--brand-green); margin-top: 12px; }

  .contact-list { position: absolute; left: 42px; top: 278px; list-style: none; }
  .contact-list li {
    display: flex; align-items: center; gap: 8px;
    height: 29px; font-size: 16.5px; color: var(--ink);
  }
  .contact-list svg { width: 15px; height: 15px; flex: none; }

  .card-back .brand { left: 0; top: 56px; width: 687px; }
  .card-back .brand-mark { width: 54px; height: 54px; background: var(--card-white); }
  .card-back .brand-name { color: var(--card-white); font-size: 42px; margin-top: 30px; }
  .card-back .brand-rule { width: 161px; background: var(--card-white); margin-top: 14px; }

  .back-url {
    position: absolute; left: 0; width: 687px; top: 344px; text-align: center;
    color: var(--card-white); font-size: 17px; letter-spacing: 2.2px;
  }
</style>
</head>
<body>

<section class="card card-front" aria-label="Card front">
  <svg class="wave" viewBox="0 0 687 393" aria-hidden="true">
    <path fill="var(--band-grey)" d="M0,0 H687 V236 C520,150 260,24 118,26 C58,27 20,48 0,72 Z"/>
    <path fill="var(--card-white)" d="M0,0 H687 V210 C520,130 260,16 118,20 C58,21 20,42 0,66 Z"/>
    <path fill="var(--brand-green)" d="M0,0 H687 V202 C520,122 260,10 118,14 C58,15 20,36 0,60 Z"/>
  </svg>

  <p class="holder-name">Derek Tolvane</p>

  <div class="brand">
    <span class="brand-mark"></span>
    <p class="brand-name">Quillmark<br>Homesteads</p>
    <span class="brand-rule"></span>
  </div>

  <ul class="contact-list">
    <li>
      <svg viewBox="0 0 16 16" aria-hidden="true"><circle cx="8" cy="8" r="7" fill="none" stroke="var(--brand-green)" stroke-width="1.4"/><path d="M5.5 4.5l1.6 0 .6 2-1 .8a5 5 0 0 0 2 2l.8-1 2 .6v1.6c-3.5.3-6.3-2.5-6-6z" fill="var(--brand-green)"/></svg>
      <span>0217394062</span>
    </li>
    <li>
      <svg viewBox="0 0 16 16" aria-hidden="true"><rect x="1" y="4" width="14" height="9" fill="var(--brand-green)"/><path d="M1 4l7 5 7-5" fill="none" stroke="#fff" stroke-width="1.2"/></svg>
      <span>dtolvane@quillmarkhomesteads.co.nz</span>
    </li>
    <li>
      <svg viewBox="0 0 16 16" aria-hidden="true"><g fill="none" stroke="var(--brand-green)" stroke-width="1.1"><circle cx="8" cy="8" r="6.5"/><ellipse cx="8" cy="8" rx="3" ry="6.5"/><path d="M1.5 8h13M2.5 4.8h11M2.5 11.2h11"/></g></svg>
      <span>www.quillmarkhomesteads.co.nz</span>
    </li>
  </ul>
</section>

<section class="card card-back" aria-label="Card back">
  <div class="brand">
    <span class="brand-mark"></span>
    <p class="brand-name">Quillmark<br>Homesteads</p>
    <span class="brand-rule"></span>
  </div>
  <p class="back-url">www.quillmarkhomesteads.co.nz</p>
</section>

</body>
</html>
```